International Career Development Workshop

I need a Powerpoint revised and designed in a more professional manner for a presentation I will be giving. We are an International Education Company that provides students with Internships Abroad, and are expanding our career development programming to offer more guidance through on-site workshops. I am happy to send along our website to showcase the colors and fonts we use, but we tend to use royal blue, lime green, and white in our color scheme. The final design should communicate opportunity and self-awareness within college students.

Target Market(s)

College Students, University Partners, and International Education Community

Industry/Entity Type

Education

Font styles to use
Sans Serif

Colors
9bcb3b
0355a3
ffffff

Requirements
Must have
• Our logo, our color scheme, a unified, professional theme throughout, Watermark of our logo, thematic sections spread across four sections.
Nice to have
• Videos and graphics
Should not have
• Spelling Errors, sloppy design

```html
<!DOCTYPE html>
<html lang="en">
<head>
<meta charset="utf-8">
<title>Career Development Workshop – Slide Template</title>
<link href="https://fonts.googleapis.com/css2?family=Lato:wght@300;400;700;900&display=swap" rel="stylesheet">
<style>
:root{
  --royal:#0e5299;
  --royal-dark:#0a4486;
  --lime:#a8d400;
  --white:#ffffff;
  --ink:#6b6b6b;
  --placeholder:#d9d9d9;
  --sheet:#000000;
}
*{box-sizing:border-box;margin:0;padding:0}
html,body{width:1061px;height:1200px;overflow:hidden;background:var(--sheet);font-family:'Lato',Arial,sans-serif}
.sheet{position:relative;width:1061px;height:1200px}
.slide{position:absolute;width:502px;height:376px;background:var(--white);overflow:hidden}
.col-a{left:22px}.col-b{left:541px}
.row-1{top:18px}.row-2{top:411px}.row-3{top:805px}

/* brand lockup */
.brand{display:flex;align-items:center;gap:6px;color:var(--royal);font-weight:700;letter-spacing:.5px;line-height:1;white-space:nowrap}
.brand .dot{width:18px;height:18px;border-radius:50%;background:var(--royal);flex:none}
.brand .name{font-size:15px}

/* cover */
.cover .hero{position:absolute;left:0;top:0;width:100%;height:269px;background:var(--royal);color:var(--white);text-align:center}
.cover h1{font-size:23px;font-weight:700;margin-top:123px}
.cover .sub{font-size:10px;font-weight:300;line-height:16px;margin:4px auto 0;width:310px}
.cover .brand{position:absolute;left:0;right:0;top:308px;justify-content:center}
.cover .brand .dot{width:30px;height:30px}
.cover .brand .name{font-size:19px}
.base-bar{position:absolute;left:0;bottom:0;width:100%;height:20px;background:var(--lime)}

/* content slides */
.header{position:absolute;left:0;top:0;width:100%;height:36px;background:var(--royal)}
.header h2{position:absolute;left:14px;top:8px;color:var(--white);font-size:17px;font-weight:700}
.header svg{position:absolute;right:0;top:0}
.header .brand{position:absolute;right:8px;top:11px}
.header .brand .dot{width:14px;height:14px}
.header .brand .name{font-size:11px}
.footer{position:absolute;left:0;bottom:0;width:100%;height:16px;background:var(--lime);color:var(--white);font-size:9.5px;line-height:16px;padding-left:13px}
.page-no{position:absolute;right:9px;bottom:4px;width:20px;height:20px;border-radius:50%;background:var(--white);border:1.5px solid var(--lime);color:var(--royal);font-size:8.5px;font-weight:900;text-align:center;line-height:17px}

.topic{position:absolute}
.topic h3{color:var(--royal);font-size:13.5px;font-weight:700;position:relative;line-height:18px}
.topic h3::before{content:"";position:absolute;left:-26px;top:2px;width:14px;height:14px;border-radius:50%;background:var(--royal);box-shadow:0 0 0 2px var(--white),0 0 0 3px var(--lime)}
.topic p{color:var(--ink);font-size:9.6px;line-height:16.3px}
.topic p+p{margin-top:16px}

/* section divider */
.divider{background:var(--royal);text-align:center;color:var(--white)}
.divider h2{font-size:34px;font-weight:700;letter-spacing:.5px;margin-top:164px;line-height:40px}
.divider .rule{width:352px;height:1.5px;background:var(--lime);margin:0 auto}
.divider .rule.top{margin-top:4px}
.divider .sub{color:var(--lime);font-size:10px;font-weight:300;line-height:22px}
.divider .base-bar{height:10px}

/* gallery */
.gallery-title{position:absolute;left:25px;top:73px;color:var(--royal);font-size:12.5px;font-weight:700;letter-spacing:.3px}
.frame{position:absolute;width:143px;height:97px;background:var(--placeholder);border:3px solid #f0f0f0;outline:1px solid #e2e2e2;color:var(--white);font-weight:900;font-size:12px;letter-spacing:1px;display:flex;align-items:center;justify-content:center}

/* closing */
.closing .panel{position:absolute;left:0;top:0;width:287px;height:100%;background:var(--royal);color:var(--white);text-align:center}
.closing h2{font-size:34px;font-weight:900;margin-top:163px;letter-spacing:.5px}
.closing .sub{font-size:10px;font-weight:300;margin-top:6px}
.closing .brand{position:absolute;left:318px;top:102px}
.closing .brand .dot{width:24px;height:24px}
.closing .brand .name{font-size:12px}
.contact{position:absolute;left:338px;top:181px;color:var(--ink);font-size:10px;line-height:16.3px;list-style:none}
.closing .base-bar{height:10px}
</style>
</head>
<body>
<main class="sheet">

  <section class="slide cover col-a row-1">
    <div class="hero">
      <h1>PROJECT TITLE HERE</h1>
      <p class="sub">Subtext here Subtext here Subtext here Subtext here Subtext here Subtext here Subtext here Subtext here</p>
    </div>
    <div class="brand"><span class="dot"></span><span class="name">HORIZON PATHWAYS</span></div>
    <div class="base-bar"></div>
  </section>

  <section class="slide col-b row-1">
    <header class="header">
      <h2>PROJECT TITLE HERE</h2>
      <svg width="190" height="42" viewBox="0 0 190 42"><polygon points="22,42 40,0 190,0 190,42" fill="#fff"/><polygon points="14,42 32,0 38,0 20,42" fill="var(--lime)"/></svg>
      <div class="brand"><span class="dot"></span><span class="name">HORIZON PATHWAYS</span></div>
    </header>
    <div class="topic" style="left:42px;top:64px;width:440px">
      <h3>Subtitle Here</h3>
      <p>chocolate chocolate cake carrot cake dragée candy canes gummies bear cake icing oat cake jelly chocolate chocolate cake carrot cake dragée candy canes gummies bear Gummies cake icing oat cake jelly chocolate chocolate cake carrot cake dragée candy canes</p>
    </div>
    <div class="topic" style="left:42px;top:159px;width:440px">
      <h3>Subtitle Here</h3>
      <p>chocolate chocolate cake carrot cake dragée candy canes gummies bear cake icing oat cake jelly chocolate chocolate cake carrot cake dragée candy canes gummies bear Gummies cake icing oat cake jelly chocolate chocolate cake carrot cake dragée candy canes</p>
    </div>
    <div class="topic" style="left:42px;top:248px;width:440px">
      <h3>Subtitle Here</h3>
      <p>chocolate chocolate cake carrot cake dragée candy canes gummies bear cake icing oat cake jelly chocolate chocolate cake carrot cake dragée candy canes gummies bear Gummies cake icing oat cake jelly chocolate chocolate cake carrot cake dragée candy canes</p>
    </div>
    <footer class="footer">Copyright text here</footer>
    <span class="page-no">01</span>
  </section>

  <section class="slide col-a row-2">
    <header class="header">
      <h2>PROJECT TITLE HERE</h2>
      <svg width="190" height="42" viewBox="0 0 190 42"><polygon points="22,42 40,0 190,0 190,42" fill="#fff"/><polygon points="14,42 32,0 38,0 20,42" fill="var(--lime)"/></svg>
      <div class="brand"><span class="dot"></span><span class="name">HORIZON PATHWAYS</span></div>
    </header>
    <div class="topic" style="left:42px;top:58px;width:205px">
      <h3>Subtitle Here</h3>
      <p>chocolate chocolate cake carrot cake dragée candy canes gummies bear cake icing oat cake jelly chocolate chocolate cake carrot cake dragée candy canes gummies bear Gummies cake icing oat cake jelly chocolate chocolate cake carrot cake dragée candy canes</p>
      <p>chocolate chocolate cake carrot cake dragée candy canes gummies bear cake icing oat cake jelly chocolate chocolate cake carrot cake dragée candy canes gummies bear Gummies cake icing oat cake jelly chocolate chocolate cake carrot cake dragée candy canes</p>
      <p>chocolate chocolate cake carrot cake dragée candy canes gummies bear cake</p>
    </div>
    <div class="topic" style="left:285px;top:58px;width:205px">
      <h3>Subtitle Here</h3>
      <p>chocolate chocolate cake carrot cake dragée candy canes gummies bear cake icing oat cake jelly chocolate chocolate cake carrot cake dragée candy canes gummies bear Gummies cake icing oat cake jelly chocolate chocolate cake carrot cake dragée candy canes</p>
      <p>chocolate chocolate cake carrot cake dragée candy canes gummies bear cake icing oat cake jelly chocolate chocolate cake carrot cake dragée candy canes gummies bear Gummies cake icing oat cake jelly chocolate chocolate cake carrot cake dragée candy canes</p>
      <p>chocolate chocolate cake carrot cake dragée candy canes gummies bear cake</p>
    </div>
    <footer class="footer">Copyright text here</footer>
    <span class="page-no">01</span>
  </section>

  <section class="slide divider col-b row-2">
    <h2>SECTION TITLE HERE</h2>
    <div class="rule top"></div>
    <p class="sub">Subtext here Subtext here Subtext here Subtext here</p>
    <div class="rule"></div>
    <div class="base-bar"></div>
  </section>

  <section class="slide col-a row-3">
    <header class="header">
      <h2>PROJECT TITLE HERE</h2>
      <svg width="190" height="42" viewBox="0 0 190 42"><polygon points="22,42 40,0 190,0 190,42" fill="#fff"/><polygon points="14,42 32,0 38,0 20,42" fill="var(--lime)"/></svg>
      <div class="brand"><span class="dot"></span><span class="name">HORIZON PATHWAYS</span></div>
    </header>
    <h3 class="gallery-title">Images Text Slide Here</h3>
    <div class="frame" role="img" aria-label="Workshop photo placeholder" style="left:24px;top:103px">IMAGE</div>
    <div class="frame" role="img" aria-label="Workshop photo placeholder" style="left:181px;top:103px">IMAGE</div>
    <div class="frame" role="img" aria-label="Workshop photo placeholder" style="left:339px;top:103px">IMAGE</div>
    <div class="frame" role="img" aria-label="Workshop photo placeholder" style="left:24px;top:218px">IMAGE</div>
    <div class="frame" role="img" aria-label="Workshop photo placeholder" style="left:181px;top:218px">IMAGE</div>
    <div class="frame" role="img" aria-label="Workshop photo placeholder" style="left:339px;top:218px">IMAGE</div>
    <footer class="footer">Copyright text here</footer>
    <span class="page-no">01</span>
  </section>

  <section class="slide closing col-b row-3">
    <div class="panel">
      <h2>THANKYOU</h2>
      <p class="sub">Subtext here Subtext here Subtext here</p>
    </div>
    <div class="brand"><span class="dot"></span><span class="name">HORIZON PATHWAYS</span></div>
    <ul class="contact">
      <li>Contact Details content here</li>
      <li>Contact Details content here</li>
      <li>Contact Details content here</li>
    </ul>
    <div class="base-bar"></div>
  </section>

</main>
</body>
</html>
```